Harbourline Physiotherapy business card design

We need a fresh, new business card design for our physiotherapy clinic Harbourline Physiotherapy

Will attach logo soon we had logo designed from our last project

Industry/Entity Type

Physical Therapy

Contact Information for Business Card

On front
Needs our logo, contact details:
58 Wexley Lane Marlow Vale NSW 2671
Ph/f: 02 9481 2057
info@harbourlinephysio.example.com.au

Requirements
Must have
• On the back of the card needs to have area to write down follow up appointments
• On front
• Needs our logo
• The colours have to be the colours in our logo which are: sky blue, black and white
• Font to be same as our logo please
• We want the card to look simple, not too cluttered but to the point
Should not have
• We don't need any extra pictures other than our logo

```html
<!DOCTYPE html>
<html lang="en">
<head>
<meta charset="utf-8">
<title>Harbourline Physiotherapy – Business Card</title>
<link rel="stylesheet" href="https://fonts.googleapis.com/css2?family=Source+Sans+3:wght@400;600;700&display=swap">
<style>
  :root {
    --page-bg: #e6e7e9;
    --card-white: #ffffff;
    --card-fade: #e4e6ea;
    --sky-blue: #2f7fd0;
    --deep-blue: #2a3fa8;
    --ink-blue: #2b5fc0;
    --text-white: #ffffff;
    --dot-line: #5a8fd6;
  }
  * { box-sizing: border-box; margin: 0; padding: 0; }
  html, body {
    width: 1200px; height: 843px; overflow: hidden;
    background: var(--page-bg);
    font-family: "Source Sans 3", "Myriad Pro", Arial, sans-serif;
  }
  .canvas { position: relative; width: 1200px; height: 843px; }

  .card {
    position: absolute; top: 266px;
    width: 540px; height: 310px;
    border-radius: 18px; overflow: hidden;
    background: linear-gradient(180deg, var(--card-white) 60%, var(--card-fade) 100%);
    box-shadow: 0 6px 18px rgba(0,0,0,0.18);
  }
  .card--back { left: 40px; }
  .card--front { left: 620px; background: var(--card-white); }

  /* Back: appointment card */
  .appt-title {
    position: absolute; top: 26px; left: 0; width: 100%;
    text-align: center; color: var(--ink-blue);
    font-size: 21px; font-weight: 600;
  }
  .appt-title::after {
    content: ""; display: block; margin: 8px auto 0;
    width: 430px; border-bottom: 1.5px dotted var(--dot-line);
  }
  .appt-row {
    position: absolute; left: 34px; right: 34px;
    display: flex; align-items: flex-end; gap: 8px;
    color: var(--ink-blue); font-size: 16px;
  }
  .appt-row .label { white-space: nowrap; }
  .appt-row .fill { flex: 1; border-bottom: 1.5px dotted var(--dot-line); height: 1px; margin-bottom: 4px; }
  .appt-row .fill--short { flex: 0 0 170px; }
  .appt-row .label--gap { margin-left: 16px; }
  .appt-row .ampm { position: absolute; right: 0; top: -8px; font-size: 11px; }
  .row-name { top: 104px; }
  .row-date { top: 146px; }
  .row-note { top: 188px; }
  .row-extra { top: 226px; }
  .appt-note {
    position: absolute; left: 40px; right: 40px; top: 252px;
    text-align: center; color: var(--ink-blue);
    font-size: 12px; line-height: 1.35;
  }

  /* Front */
  .front-art { position: absolute; inset: 0; width: 540px; height: 310px; }
  .brand {
    position: absolute; top: 52px; left: 150px;
    display: flex; align-items: center; gap: 12px;
  }
  .brand-dot {
    width: 34px; height: 34px; border-radius: 50%;
    background: var(--sky-blue); flex: none;
  }
  .brand-name {
    color: var(--sky-blue); font-size: 29px; font-weight: 600;
    line-height: 1.0;
  }
  .holder {
    position: absolute; left: 26px; top: 146px;
    color: var(--text-white); font-size: 15px; line-height: 1.3;
  }
  .holder-name { font-size: 20px; font-weight: 600; margin-bottom: 2px; }
  .contacts {
    position: absolute; right: 16px; top: 222px;
    list-style: none; color: var(--text-white); font-size: 14px;
  }
  .contacts li {
    display: flex; justify-content: flex-end; align-items: center;
    gap: 8px; height: 19px;
  }
  .contacts svg { width: 13px; height: 13px; flex: none; }
</style>
</head>
<body>
<main class="canvas">

  <section class="card card--back" aria-label="Appointment card, back">
    <h2 class="appt-title">Next Appointment</h2>
    <div class="appt-row row-name">
      <span class="label">Name :</span><span class="fill fill--short"></span>
      <span class="label label--gap">Time :</span><span class="fill"></span>
      <span class="ampm">AM/PM</span>
    </div>
    <div class="appt-row row-date"><span class="label">Date :</span><span class="fill"></span></div>
    <div class="appt-row row-note"><span class="label">Note :</span><span class="fill"></span></div>
    <div class="appt-row row-extra"><span class="fill"></span></div>
    <p class="appt-note">Please give me 24 hours notice if you are unable to keep your appointment or wish to reschedule.</p>
  </section>

  <section class="card card--front" aria-label="Business card, front">
    <svg class="front-art" viewBox="0 0 540 310" aria-hidden="true">
      <defs>
        <linearGradient id="bandBlue" x1="0" y1="0" x2="1" y2="0.4">
          <stop offset="0" stop-color="#2a3fa8"/>
          <stop offset="0.55" stop-color="#2f6fcc"/>
          <stop offset="1" stop-color="#2a3fa8"/>
        </linearGradient>
        <linearGradient id="swooshGrey" x1="0" y1="0" x2="1" y2="0">
          <stop offset="0" stop-color="#4b4e53"/>
          <stop offset="0.5" stop-color="#a4a7ab"/>
          <stop offset="1" stop-color="#4b4e53"/>
        </linearGradient>
      </defs>
      <path d="M0,110 C180,124 380,160 540,186 L540,198 C380,172 180,136 0,122 Z" fill="url(#swooshGrey)"/>
      <path d="M0,130 C180,144 380,180 540,206 L540,310 L0,310 Z" fill="url(#bandBlue)"/>
    </svg>

    <div class="brand">
      <span class="brand-dot"></span>
      <span class="brand-name">Harbourline<br>Physiotherapy</span>
    </div>

    <div class="holder">
      <p class="holder-name">Daniel Reeve</p>
      <p>CEO/Founder</p>
      <p>58 Wexley Lane Marlow Vale</p>
      <p>NSW 2671</p>
    </div>

    <ul class="contacts">
      <li>02 9481 2057
        <svg viewBox="0 0 16 16" aria-label="Phone"><path fill="#fff" d="M3.5 1.5l2.5 0 1 3.5-1.6 1.2c.8 1.8 2.2 3.2 4 4l1.2-1.6 3.4 1v2.6c0 .9-.8 1.5-1.6 1.4C6.8 13 3 9.2 2.1 3.6 2 2.300 2.6 1.5 3.5 1.5z"/></svg>
      </li>
      <li>02 9481 2057
        <svg viewBox="0 0 16 16" aria-label="Fax"><rect x="4" y="1.5" width="8" height="4" fill="#fff"/><rect x="1.5" y="6" width="13" height="6" rx="1" fill="#fff"/><rect x="4" y="10" width="8" height="4.5" fill="#fff" stroke="#2a3fa8" stroke-width="1"/></svg>
      </li>
      <li>info@harbourlinephysio.example.com.au
        <svg viewBox="0 0 16 16" aria-label="Email"><rect x="1.5" y="3.5" width="13" height="9" rx="1" fill="#fff"/><path d="M2 4.5l6 4.5 6-4.5" fill="none" stroke="#2a3fa8" stroke-width="1.2"/></svg>
      </li>
      <li>www.harbourlinephysio.example.com.au
        <svg viewBox="0 0 16 16" aria-label="Website"><circle cx="8" cy="8" r="6.5" fill="#fff"/><path d="M1.5 8h13M8 1.5c-2.5 3-2.5 10 0 13M8 1.5c2.5 3 2.5 10 0 13" fill="none" stroke="#2a3fa8" stroke-width="1"/></svg>
      </li>
    </ul>
  </section>

</main>
</body>
</html>
```